RW Framewell Inc Business cards

We need business cards using our existing logo but slightly modified. Right now the logo says RW Loadbearing Masonry. We want to keep the RW part of the design, but replace the Structural Concrete portion with "FRAMEWELL". Please see the attached file.
Ideally this would be a blank template so we can add Different Names, titles, and phone numbers later.
On the one side we want only the logo and on the other side the detail. I'm attaching an example for you to see.
Please reach out with any other questions. Our address and other details will be given out once we find a design we like.

Target Market(s)

Construction Industry

```html
<!DOCTYPE html>
<html lang="en">
<head>
<meta charset="utf-8">
<title>RW Framewell Inc Business Cards</title>
<link rel="stylesheet" href="https://fonts.googleapis.com/css2?family=Montserrat:wght@600&family=Roboto:wght@400&display=swap">
<style>
  :root {
    --page-bg: #e3e3e3;
    --card-white: #f7f7f7;
    --brand-blue: #2d5fa6;
    --brand-grey: #6b6b6b;
    --text-grey: #5a5a5a;
    --white: #ffffff;
  }
  * { margin: 0; padding: 0; box-sizing: border-box; }
  html, body { width: 1200px; height: 852px; overflow: hidden; }
  body {
    background: var(--page-bg);
    position: relative;
    font-family: "Roboto", Arial, sans-serif;
  }
  .card {
    position: absolute;
    top: 276px;
    width: 525px;
    height: 300px;
    border-radius: 22px;
    overflow: hidden;
    background: var(--card-white);
    box-shadow: 0 4px 14px rgba(0,0,0,0.18);
  }
  .card--front { left: 60px; }
  .card--back { left: 615px; }

  /* Front */
  .front-band {
    position: absolute; left: 0; right: 0; bottom: 0; height: 14px;
    display: flex;
  }
  .front-band__grey { width: 42%; background: var(--brand-grey); }
  .front-band__blue { flex: 1; background: var(--brand-blue); }

  .wordmark {
    position: absolute;
    font-family: "Montserrat", Arial, sans-serif;
    font-weight: 600;
    text-align: left;
    line-height: 1;
  }
  .wordmark__initials { display: block; font-size: 78px; letter-spacing: 2px; }
  .wordmark__name { display: block; font-size: 24px; letter-spacing: 7px; margin-top: 6px; }
  .card--front .wordmark { left: 150px; top: 88px; color: var(--brand-blue); }

  /* Back */
  .back-white { position: absolute; left: 0; right: 0; top: 0; height: 100px; background: var(--card-white); }
  .back-grey { position: absolute; left: 0; right: 0; top: 100px; height: 12px; background: var(--brand-grey); }
  .back-blue { position: absolute; left: 0; right: 0; top: 112px; bottom: 0; background: var(--brand-blue); }

  .holder { position: absolute; left: 30px; top: 46px; }
  .holder__name {
    font-family: "Montserrat", Arial, sans-serif;
    font-weight: 600; font-size: 19px; color: var(--brand-blue);
  }
  .holder__title { font-size: 12.5px; color: var(--text-grey); margin-top: 3px; margin-left: 12px; }

  .contact {
    position: absolute; left: 30px; top: 150px;
    color: var(--white); font-size: 13px; line-height: 1.45;
  }
  .contact__address { margin-bottom: 8px; }
  .contact__row { display: flex; align-items: center; gap: 10px; }
  .contact__row svg { width: 12px; height: 12px; flex: none; }

  .card--back .wordmark { left: 305px; top: 150px; color: var(--white); }
  .card--back .wordmark__initials { font-size: 62px; }
  .card--back .wordmark__name { font-size: 18px; letter-spacing: 5px; }
</style>
</head>
<body>
  <section class="card card--front" aria-label="Card front">
    <div class="wordmark">
      <span class="wordmark__initials">RW</span>
      <span class="wordmark__name">FRAMEWELL</span>
    </div>
    <div class="front-band">
      <div class="front-band__grey"></div>
      <div class="front-band__blue"></div>
    </div>
  </section>

  <section class="card card--back" aria-label="Card back">
    <div class="back-white"></div>
    <div class="back-grey"></div>
    <div class="back-blue"></div>

    <div class="holder">
      <p class="holder__name">Alan RW Tate</p>
      <p class="holder__title">Managing Director</p>
    </div>

    <div class="contact">
      <p class="contact__address">58 Beam Row, Millbrook,<br>Ohio, US 440210</p>
      <p class="contact__row">
        <svg viewBox="0 0 12 12" aria-hidden="true"><path fill="#fff" d="M2.5 1h2l1 3-1.3 1a6.5 6.5 0 0 0 2.8 2.8l1-1.3 3 1v2c0 .6-.4 1-1 1A9.5 9.5 0 0 1 1.5 2c0-.6.4-1 1-1z"/></svg>
        555-204-7780
      </p>
      <p class="contact__row">
        <svg viewBox="0 0 12 12" aria-hidden="true"><rect x="0.5" y="2" width="11" height="8" fill="#fff"/><path d="M0.5 2l5.5 4.5L11.5 2" fill="none" stroke="#2d5fa6" stroke-width="1"/></svg>
        alan@framewellco.com
      </p>
      <p class="contact__row">
        <svg viewBox="0 0 12 12" aria-hidden="true"><circle cx="6" cy="6" r="5" fill="none" stroke="#fff" stroke-width="1.2"/><path d="M1 6h10M6 1c-2.5 3-2.5 7 0 10M6 1c2.5 3 2.5 7 0 10" fill="none" stroke="#fff" stroke-width="1"/></svg>
        www.framewellco.com
      </p>
    </div>

    <div class="wordmark">
      <span class="wordmark__initials">RW</span>
      <span class="wordmark__name">FRAMEWELL</span>
    </div>
  </section>
</body>
</html>
```